National Mission Critical Construction Contractor needs Stationery Design to make a bold statement

We are a small commercial construction company, working primarily in mission critical facilities across the U.S.. We have exciting corporate changes going an and a new logo and office space so we need new stationery. The final design should incorporate our new logo and invoke a fresh, high-tech feel while looking simple and modern.

Industry/Entity Type

Construction

Contact Information for Business Card

We are required to list our state licensing qualifications on the back of our card.

Font styles to use
Sans Serif

Requirements
Must have
• We need to have a design for second page of stationery, envelopes both standard and with a window and for a 3 x 4 notepad.

```html
<!DOCTYPE html>
<html lang="en">
<head>
<meta charset="utf-8">
<title>Cedar Line Construction Management – Stationery</title>
<link href="https://fonts.googleapis.com/css2?family=PT+Sans:wght@400;700&family=Saira+Semi+Condensed:wght@700&display=swap" rel="stylesheet">
<style>
:root{
  --backdrop:#a9a8aa;
  --paper:#f4f3f1;
  --white:#ffffff;
  --brand-blue:#1272bb;
  --sky-blue:#29a3dc;
  --leaf-green:#8cc63f;
  --ink:#4a4a4a;
  --text-font:"PT Sans", Arial, sans-serif;
  --title-font:"Saira Semi Condensed", "PT Sans", sans-serif;
}
*{box-sizing:border-box;margin:0;padding:0}
html,body{width:1160px;height:1200px;overflow:hidden}
body{background:var(--backdrop);font-family:var(--text-font);color:var(--ink);position:relative}
.sheet{position:absolute;background:var(--paper);box-shadow:0 2px 6px rgba(0,0,0,.25);overflow:hidden}
.wordmark{font-family:var(--text-font);font-weight:700;color:var(--brand-blue);text-transform:uppercase;letter-spacing:.02em;line-height:1}
.tagline{font-family:var(--text-font);color:var(--brand-blue);text-transform:uppercase;letter-spacing:.22em;line-height:1}
.brand{position:absolute;text-align:center}
.brand .wordmark{border-bottom:1px solid #c9c9c9;padding-bottom:3px}
.brand .tagline{margin-top:3px}
.icon{width:7px;height:7px;fill:var(--brand-blue);vertical-align:-1px;margin-right:5px}
.wave{position:absolute;left:0;bottom:0;display:block}

/* Letterhead */
.letterhead{left:70px;top:71px;width:474px;height:666px}
.letterhead .brand{left:40px;top:86px;width:110px}
.letterhead .wordmark{font-size:14px}
.letterhead .tagline{font-size:4px;letter-spacing:.16em}
.letterhead .contact{position:absolute;left:332px;top:40px;font-size:7.4px;line-height:10.8px}
.letterhead .contact .address{margin-bottom:5px}
.letter{position:absolute;left:47px;top:186px;width:381px}
.letter .salutation{font-size:12px;margin-bottom:22px}
.letter p{font-size:6.5px;line-height:11.3px;text-align:justify;margin-bottom:11.3px}
.letter .closing{font-size:6.5px;margin-top:23px}
.letter .signature{display:block;margin:6px 0 4px}
.letter .signer{font-size:7.2px;line-height:12px;padding-left:3px}

/* Folder */
.folder{left:580px;top:38px;width:502px;height:710px}
.folder .strip{position:absolute;left:0;top:0}
.folder .brand{left:140px;top:174px;width:238px}
.folder .wordmark{font-size:30px}
.folder .tagline{font-size:9.5px;letter-spacing:.2em;margin-top:5px}
.folder .title{position:absolute;left:130px;top:488px;width:268px;text-align:center;font-family:var(--title-font);font-weight:700;font-size:27px;color:var(--brand-blue)}

/* Envelopes */
.envelope-back{left:154px;top:802px;width:530px;height:242px;background:var(--white)}
.envelope-back .flap{position:absolute;left:0;top:0}
.envelope-back .web{position:absolute;left:0;top:60px;width:530px;text-align:center;color:var(--white);font-size:8px}
.envelope-front{left:87px;top:910px;width:531px;height:241px}
.envelope-front .brand{left:22px;top:52px;width:96px}
.envelope-front .wordmark{font-size:12.5px}
.envelope-front .tagline{font-size:3.6px;letter-spacing:.14em}
.envelope-front .address{position:absolute;left:10px;top:80px;width:120px;text-align:center;font-size:8px;line-height:11px}

/* Business cards */
.card{position:absolute;width:318px;height:181px;border-radius:8px;overflow:hidden;box-shadow:0 2px 6px rgba(0,0,0,.2)}
.card-front{left:758px;top:780px;background:var(--white)}
.card-front .brand{left:82px;top:33px;width:154px}
.card-front .wordmark{font-size:20px}
.card-front .tagline{font-size:5.6px;letter-spacing:.18em}
.card-band{position:absolute;left:0;top:103px;width:318px;height:67px;background:linear-gradient(90deg,var(--brand-blue) 0 50%,var(--sky-blue) 50% 100%)}
.card-band .person{position:absolute;left:13px;top:8px;color:var(--white);font-size:8px;line-height:12.4px}
.card-band .person .name{font-weight:700;font-size:11px;letter-spacing:.02em;line-height:13px}
.card-band .lines{position:absolute;right:13px;top:8px;color:var(--white);font-size:7.8px;line-height:12.2px;text-align:right}
.card-band .lines .icon{fill:var(--white);margin:0 0 0 4px}
.card-back{left:758px;top:974px;background:var(--brand-blue)}
.card-back .brand{left:86px;top:99px;width:146px}
.card-back .wordmark{font-size:18px;color:var(--white);border-bottom-color:rgba(255,255,255,.6)}
.card-back .tagline{font-size:5.4px;color:var(--white);letter-spacing:.16em}
</style>
</head>
<body>

<svg width="0" height="0" style="position:absolute" aria-hidden="true">
  <defs>
    <symbol id="i-phone" viewBox="0 0 10 10"><path d="M2 0.5 L3.6 2.8 L2.7 3.8 C3.3 5.2 4.8 6.7 6.2 7.3 L7.2 6.4 L9.5 8 L8.4 9.5 C4.5 9.3 0.7 5.5 0.5 1.6Z"/></symbol>
    <symbol id="i-mobile" viewBox="0 0 10 10"><path d="M2.5 0 H7.5 V10 H2.5Z M3.4 1 V8 H6.6 V1Z"/></symbol>
    <symbol id="i-fax" viewBox="0 0 10 10"><path d="M2.5 0.5 H7.5 V3.5 H2.5Z M0.5 4 H9.5 V8 H8 V6.5 H2 V8 H0.5Z M2.5 7 H7.5 V9.5 H2.5Z"/></symbol>
    <symbol id="i-mail" viewBox="0 0 10 10"><path d="M0.5 2 H9.5 V8 H0.5Z" /><path d="M0.8 2.3 L5 5.5 L9.2 2.3" fill="none" stroke="#fff" stroke-width="0.9"/></symbol>
    <symbol id="i-web" viewBox="0 0 10 10"><circle cx="5" cy="5" r="4.5"/><path d="M0.5 5 H9.5 M5 0.5 C2.8 3 2.8 7 5 9.5 M5 0.5 C7.2 3 7.2 7 5 9.5" fill="none" stroke="#fff" stroke-width="0.7"/></symbol>
  </defs>
</svg>

<!-- Letterhead -->
<section class="sheet letterhead">
  <div class="brand">
    <div class="wordmark">Cedar Line</div>
    <div class="tagline">Construction Management</div>
  </div>
  <div class="contact">
    <div class="address">4120 Harbor View Road<br>Juneau, Alaska 99801</div>
    <div><svg class="icon"><use href="#i-phone"/></svg>907 555 0142</div>
    <div><svg class="icon"><use href="#i-mobile"/></svg>907 555 0187</div>
    <div><svg class="icon"><use href="#i-fax"/></svg>907 555 0163</div>
    <div><svg class="icon"><use href="#i-mail"/></svg>office@cedarlinecm.com</div>
    <div><svg class="icon"><use href="#i-web"/></svg>www.cedarlinecm.com</div>
  </div>
  <div class="letter">
    <div class="salutation">Dear Mr. Reyes,</div>
    <p>Thank you for meeting with our team last week to review the plans for your new data center campus. We appreciated the chance to walk the site and hear your goals for uptime, power density and schedule. Our group has delivered similar critical facilities across the country, and we are confident we can support you at every stage.</p>
    <p>Enclosed you will find a summary of our approach, including preconstruction services, phasing options and a preliminary budget. Each section is built around keeping your existing operations online while new work moves forward. We have also listed the key staff who would be assigned to the project full time.</p>
    <p>Safety and quality remain at the center of everything we build. Our field teams follow a strict commissioning process, and every system is tested before it is turned over to your facility staff. We keep owners informed with weekly reports, clear cost tracking and open access to our project managers. This level of communication has helped our clients avoid delays and make confident decisions throughout construction.</p>
    <p>Please let us know if you would like to schedule a follow up meeting or a tour of one of our recently completed facilities. We look forward to the opportunity to build this project with you and your team.</p>
    <div class="closing">Sincerely,</div>
    <svg class="signature" width="64" height="22" viewBox="0 0 64 22" aria-hidden="true">
      <path d="M1 12 C15 10 30 9 46 11 C55 12 62 14 58 16 M30 4 C34 6 36 10 35 18 C34 20 38 19 40 17" fill="none" stroke="#222" stroke-width="1"/>
    </svg>
    <div class="signer">Daniel Reyes<br>CEO/ Founder</div>
  </div>
  <svg class="wave" width="474" height="70" viewBox="0 0 474 70" aria-hidden="true">
    <path d="M0 13 C110 52 250 42 474 18" fill="none" stroke="var(--leaf-green)" stroke-width="3"/>
    <path d="M0 20 C110 60 250 50 474 25 L474 70 L0 70Z" fill="var(--brand-blue)"/>
  </svg>
</section>

<!-- Presentation folder -->
<section class="sheet folder">
  <svg class="strip" width="60" height="710" viewBox="0 0 60 710" aria-hidden="true">
    <path d="M38 0 C48 120 50 200 32 330 C16 460 24 600 52 710" fill="none" stroke="var(--leaf-green)" stroke-width="3"/>
    <path d="M0 0 L35 0 C45 120 47 200 29 330 C13 460 21 600 48 710 L0 710Z" fill="var(--brand-blue)"/>
  </svg>
  <div class="brand">
    <div class="wordmark">Cedar Line</div>
    <div class="tagline">Construction Management</div>
  </div>
  <div class="title">Project Cover Sheet</div>
</section>

<!-- Envelope, back -->
<section class="sheet envelope-back">
  <svg class="flap" width="530" height="90" viewBox="0 0 530 90" aria-hidden="true">
    <path d="M0 0 H530 L520 60 C517 76 506 88 488 88 H42 C24 88 13 76 10 60Z" fill="var(--brand-blue)"/>
  </svg>
  <div class="web">www.cedarlinecm.com</div>
</section>

<!-- Envelope, front -->
<section class="sheet envelope-front">
  <div class="brand">
    <div class="wordmark">Cedar Line</div>
    <div class="tagline">Construction Management</div>
  </div>
  <div class="address">4120 Harbor View Road<br>Juneau, Alaska 99801</div>
  <svg class="wave" width="531" height="70" viewBox="0 0 531 70" aria-hidden="true">
    <path d="M0 10 C130 52 280 40 531 6" fill="none" stroke="var(--leaf-green)" stroke-width="3"/>
    <path d="M0 17 C130 60 280 48 531 14 L531 70 L0 70Z" fill="var(--brand-blue)"/>
  </svg>
</section>

<!-- Business card, front -->
<section class="card card-front">
  <div class="brand">
    <div class="wordmark">Cedar Line</div>
    <div class="tagline">Construction Management</div>
  </div>
  <div class="card-band">
    <div class="person">
      <div class="name">DANIEL REYES</div>
      <div>CEO/Founder</div>
      <div>4120 Harbor View Road</div>
      <div>Juneau, Alaska 99801</div>
    </div>
    <div class="lines">
      <div>907 555 0142<svg class="icon"><use href="#i-phone"/></svg></div>
      <div>907 555 0187<svg class="icon"><use href="#i-mobile"/></svg></div>
      <div>907 555 0163<svg class="icon"><use href="#i-fax"/></svg></div>
      <div>office@cedarlinecm.com<svg class="icon"><use href="#i-mail"/></svg></div>
    </div>
  </div>
</section>

<!-- Business card, back -->
<section class="card card-back">
  <div class="brand">
    <div class="wordmark">Cedar Line</div>
    <div class="tagline">Construction Management</div>
  </div>
</section>

</body>
</html>
```